Property management company looking for modern card design

We at Blue Heron Partners provides property management services for its residential and commercial properties, with expertise in all categories of multifamily, industrial and office projects throughout California.

We need a business card design that is professional and modern designed business card. In our field, clients get hundreds of business cards, we would like our card to stand out.

Please avoid small print.

Target Market(s)

Professionals and high end clients

Industry/Entity Type

Financial Planning

Contact Information for Business Card

Company Name: Blue Heron Partners, Name, email, license #, phone number, website blueheronpartners.com

Font styles to use
Sans Serif

Requirements
Must have
• The card design needs to be adaptable because there is a possibly we will be expanding into different sectors other than real estate. The card design should be focused on financial planning and asset management.
Nice to have
• Modern and simple business card. Eye catching. Non-standard size/shaped cards would be great.
• blueheronpartners.com
Should not have
• Too many bright color or any pictures or shapes of real estate stuff.

```html
<!DOCTYPE html>
<html lang="en">
<head>
<meta charset="utf-8">
<title>Blue Heron Partners – Business Card</title>
<link href="https://fonts.googleapis.com/css2?family=Arimo:wght@400&family=PT+Sans+Narrow:wght@400&display=swap" rel="stylesheet">
<style>
  :root {
    --backdrop: #dccab3;
    --card: #efebe2;
    --accent: #d71f2b;
    --ink: #1c1c1c;
  }
  html, body {
    margin: 0;
    padding: 0;
    width: 1200px;
    height: 823px;
    overflow: hidden;
    background: var(--backdrop);
  }
  .canvas {
    position: relative;
    width: 1200px;
    height: 823px;
    display: flex;
    align-items: center;
    justify-content: center;
    gap: 40px;
  }
  .card {
    position: relative;
    width: 520px;
    height: 297px;
    background: var(--card);
    box-shadow: 0 6px 18px rgba(0,0,0,0.12);
    overflow: hidden;
  }
  .card-graphics {
    position: absolute;
    inset: 0;
  }
  .brand {
    position: absolute;
    display: flex;
    flex-direction: column;
    align-items: center;
    gap: 14px;
  }
  .brand-mark {
    width: 96px;
    height: 96px;
    border-radius: 50%;
    background: var(--accent);
  }
  .brand-name {
    font-family: "Arimo", sans-serif;
    font-weight: 400;
    color: var(--accent);
    font-size: 19px;
    letter-spacing: 3px;
    text-align: center;
    line-height: 1.25;
  }
  .card-back .brand {
    left: 0;
    right: 0;
    top: 62px;
  }
  .card-front .brand {
    left: 22px;
    width: 190px;
    top: 60px;
  }
  .card-front .brand-mark {
    width: 88px;
    height: 88px;
  }
  .brand-name-front {
    font-size: 17px;
  }
  .contact {
    position: absolute;
    left: 318px;
    top: 34px;
    right: 14px;
  }
  .contact-name {
    font-family: "PT Sans Narrow", sans-serif;
    color: var(--accent);
    font-size: 27px;
    margin: 0 0 52px;
    font-weight: 400;
  }
  .contact-list {
    list-style: none;
    margin: 0;
    padding: 0;
    font-family: "Arimo", sans-serif;
    color: var(--ink);
    font-size: 17px;
    line-height: 1.45;
  }
  .contact-license {
    margin-top: 6px;
  }
</style>
</head>
<body>
<main class="canvas">

  <section class="card card-back" aria-label="Card back">
    <div class="brand">
      <div class="brand-mark"></div>
      <div class="brand-name">BLUE HERON<br>PARTNERS</div>
    </div>
  </section>

  <section class="card card-front" aria-label="Card front">
    <svg class="card-graphics" width="520" height="297" viewBox="0 0 520 297" aria-hidden="true">
      <path class="accent-arc" d="M172,0 Q335,130 240,297 L224,297 Q315,130 150,0 Z" fill="var(--accent)"/>
    </svg>
    <div class="brand">
      <div class="brand-mark"></div>
      <div class="brand-name brand-name-front">BLUE HERON<br>PARTNERS</div>
    </div>
    <div class="contact">
      <h1 class="contact-name">Daniel Ortiz</h1>
      <ul class="contact-list">
        <li>555-014-2297</li>
        <li>dan@bhpartners.com</li>
        <li>blueheronpartners.com</li>
        <li class="contact-license">Lic : 20480153</li>
      </ul>
    </div>
  </section>

</main>
</body>
</html>
```